Book Title: “Faith: Road of Endless Grace” Please see the attachment “Text on the cover”.

Book Cover Design Instructions: This book is meant for people of all religions and nationalities. Therefore, on the cover, there should be no mosque or an object specific to any religion. The primary emphasis should be on the "Boundless Mercy of Heaven." Therefore, use universal symbols of love. The second priority themes could be Sufism, Peace, and self-improvement. Rest is your imagination. Please also see the attachment: 'Book description and author's Bio.'
This book has the potential to be a best seller. Please do a good job.
What Book Cover Formats are required: A designer should submit cover designs in three formats: (1) eBook, (2) Paperback, and (3) Hardback. These books will be published on Borvex QPL.
Format requirements for eBooks are available from: https://qpl.borvex.example/en_US/help/topic/R731928457.
You can find paperback and hardback cover measurements from: https://qpl.borvex.example/en_US/cover-calculator
• To complete the project, all three formats should be accepted by Borvex QPL.
• The book interior trim size is 6.14 X 9.21 inches.
• Interior Type: Premium color.
• No bleed.
• I do not upload barcode. So, the back cover should have room for Borvex to print the barcode.
• Number of pages 126.
Compensation for the designer: After selecting one designer, I will increase the amount by $200 on Artvelle to compensate for three deliverables.
Follow-up of the Project:
After the book is published, I may need minor revisions. For example, the number of pages may change. Therefore, I will need the same design in revised sizes. In that case, I will pay $25 for each revision. For example, if the number of pages changes, I will need a different spine for paperback and hardback, then I will pay the artist $25 + $25 = $50 for both designs.
List of Enclosers:
1. Text on the cover.
2. Book description and author's Bio for the back cover.
3. Later, I will upload my picture for the book's back cover.

Target Market(s)

Any adult

Industry/Entity Type

Any industry

Requirements
Must have
• Three Deliverables

```html
<!DOCTYPE html>
<html lang="en">
<head>
<meta charset="utf-8">
<title>Faith: Road of Endless Grace — Book Cover</title>
<link href="https://fonts.googleapis.com/css2?family=Bebas+Neue&family=Montserrat:wght@500;600&display=swap" rel="stylesheet">
<style>
  :root {
    --page-bg: #ffffff;
    --cover-navy: #1c1760;
    --band-yellow: #ffe800;
    --band-text: #1c1896;
    --ink-white: #ffffff;
    --accent-yellow: #ffe800;
  }
  html, body {
    margin: 0;
    padding: 0;
    width: 1200px;
    height: 1200px;
    overflow: hidden;
    background: var(--page-bg);
  }
  .cover-canvas {
    display: block;
    width: 1200px;
    height: 1200px;
  }
  .cover-panel { fill: var(--cover-navy); }
  .title-band { fill: var(--band-yellow); }
  .display-word { font-family: "Bebas Neue", "Oswald", sans-serif; }
  .title-faith { fill: var(--ink-white); }
  .title-road { fill: var(--accent-yellow); }
  .title-endless { fill: var(--band-text); }
  .title-grace {
    font-family: "Montserrat", Arial, sans-serif;
    font-weight: 600;
    fill: var(--ink-white);
  }
  .kicker, .subtitle, .author {
    font-family: "Montserrat", Arial, sans-serif;
    font-weight: 500;
    fill: var(--ink-white);
  }
  .subtitle-accent { fill: var(--accent-yellow); }
  .rule { stroke: url(#ruleFade); stroke-width: 1.2; }
</style>
</head>
<body>
<svg class="cover-canvas" viewBox="0 0 1200 1200" xmlns="http://www.w3.org/2000/svg" role="img" aria-label="Book cover: Faith: Road of Endless Grace by Dr. Selim Hardaway">
  <defs>
    <linearGradient id="ruleFade" x1="0" x2="1" y1="0" y2="0">
      <stop offset="0" stop-color="#ffffff" stop-opacity="0"/>
      <stop offset="0.5" stop-color="#ffffff" stop-opacity="0.85"/>
      <stop offset="1" stop-color="#ffffff" stop-opacity="0"/>
    </linearGradient>
  </defs>

  <rect class="cover-panel" x="295" y="141" width="618" height="925"/>

  <text class="kicker" x="604" y="182" text-anchor="middle" font-size="27" textLength="456" lengthAdjust="spacingAndGlyphs">BOUNDLESS MERCY OF HEAVEN</text>

  <text class="display-word title-faith" x="604" y="342" text-anchor="middle" font-size="197" textLength="366" lengthAdjust="spacingAndGlyphs">FAITH</text>

  <text class="display-word title-road" x="604" y="521" text-anchor="middle" font-size="217" textLength="536" lengthAdjust="spacingAndGlyphs">ROAD OF</text>

  <rect class="title-band" x="295" y="544" width="618" height="181"/>
  <text class="display-word title-endless" x="604" y="708" text-anchor="middle" font-size="210" textLength="528" lengthAdjust="spacingAndGlyphs">ENDLESS</text>

  <text class="title-grace" x="604" y="880" text-anchor="middle" font-size="190" textLength="533" lengthAdjust="spacingAndGlyphs">GRACE</text>

  <line class="rule" x1="420" y1="919" x2="790" y2="919"/>
  <text class="subtitle" x="604" y="953" text-anchor="middle" font-size="32" textLength="528" lengthAdjust="spacingAndGlyphs">A JOURNEY TOWARD A CALMER</text>
  <text class="subtitle" x="604" y="992" text-anchor="middle" font-size="32" textLength="494" lengthAdjust="spacingAndGlyphs">HEART <tspan class="subtitle-accent">AND GRATEFUL LIVING</tspan></text>
  <line class="rule" x1="420" y1="1003" x2="790" y2="1003"/>

  <text class="author" x="604" y="1047" text-anchor="middle" font-size="30" textLength="347" lengthAdjust="spacingAndGlyphs">DR. SELIM HARDAWAY</text>
</svg>
</body>
</html>
```